Logo and Website Design for QR.KA Horizon - a Software Engineering and IT company

Software engineering and IT are two different disciplines - and yet inseparably linked. At QR.KA Horizon, we combine both worlds and ensure that our software solutions are not only innovative and powerful, but also integrate perfectly into existing IT landscapes. Vision stands more for imagination, so it is not neccessary something what has to do with visualisation. Please consider that the winning competitor is also instructed to make a logo for the company. So please make a suitable logo for QR.KA Horizon to which the website fits to and show it during the website creation process. A good Logo desing is important for winning the competition. The website should contain a landing page with inspiring, perhaps futuristic photos of a datacenter and lines of code. Eventuelly flewent integrated in the text. On the landing page the company should introduced with a small text (max 250 words) followed by a section with a short text to one of our products nearby a graphic visualising the architecture of the product. The menue should be on top and fixed during scrolling and consist of the menue items home, solutions, who are we and a contact button. There should be a footer for linking social media, rights and Impressum. Only as an idea not a must. The very first view on the landing page could also be the menue bar and below of it a transparent unsharp photo (e.g. datacenter, lines of code, both ;) with the company name in the center.

###############################################################

Hi Designers,

Despite your very good approaches for describing QR.KA Horizon, here a short introduction (german text) from ourself:

------
QR.KA Horizon – Ihr Partner für ganzheitliche Softwarelösungen

Die QR.KA Horizon ist ein dynamisches Unternehmen, das sich nicht nur auf die Konzeption, das Design und die Entwicklung maßgeschneiderter Software spezialisiert hat, sondern auch deren reibungslosen Betrieb sicherstellt. Mit einem Team aus erfahrenen Softwarearchitekten und IT-Professionals verbinden wir modernste Softwareentwicklung mit tiefgehendem IT-Know-how – für Lösungen, die nachhaltig, leistungsstark und zukunftssicher sind.

Software Engineering trifft IT – Perfektion in Kombination
Software Engineering und IT sind zwei unterschiedliche Disziplinen – und doch untrennbar miteinander verbunden. Wir bei QR.KA Horizon vereinen beide Welten und sorgen dafür, dass unsere Softwarelösungen nicht nur innovativ und leistungsfähig sind, sondern sich auch perfekt in bestehende IT-Landschaften integrieren.

Expertise mit Fokus auf Healthcare & komplexe IT-Umgebungen
Unsere Experten bringen jahrzehntelange Erfahrung aus dem Healthcare-Sektor mit und unterstützen IT-Abteilungen großer Kliniken in der Entwicklung und Optimierung von Softwarelösungen. Von Anwendungssoftware bis hin zu Steuerungssystemen – unsere Softwareingenieure wissen genau, worauf es ankommt.

Ganzheitlicher Ansatz – über die Software hinaus
Wir entwickeln nicht nur Software, sondern übernehmen auch die Verantwortung für deren stabile und effiziente Betriebsumgebung. Egal, ob on-premises, in der Cloud oder als SaaS-Lösung – wir kümmern uns um den kompletten Lifecycle Ihrer Anwendung.

Ihre Vision – unsere Mission.
Ob Neuentwicklung einer SaaS-Anwendung oder die Migration bestehender Lösungen in eine moderne SaaS-Umgebung – mit QR.KA Horizon haben Sie einen starken Partner an Ihrer Seite.

Lassen Sie uns gemeinsam die Zukunft Ihrer Software gestalten!
--------------

Our first solution called "Clear Record Transfer Gateway" (CLURA)
-------------------
Teilen Sie Ihre Daten sicher – ohne Kompromisse!

Sie nutzen eine relationale Datenbank (Brightcask, Tabulon Hub, Vellumdb etc.) und möchten ausgewählte Daten mit Dritten teilen – sei es für ein Data Warehouse, Business Controller, Lieferanten oder Kunden? Doch dabei sollen Datensicherheit, Integrität und Verfügbarkeit Ihrer primären Lösung in keiner Weise gefährdet werden?

Mit unserer Lösung erhalten Sie genau das: Maximalen Schutz für Ihre Anwendung bei gleichzeitigem Nutzen durch autorisierte Dritte – ganz ohne teure Lizenzkosten für eine Schattendatenbank.

Lassen Sie uns gemeinsam herausfinden, wie Sie Ihre Daten sicher und effizient nutzen können. Kontaktieren Sie uns – wir zeigen Ihnen, was möglich ist!
---------------------

Our second solution MIVO:
---------------------
MIVO – Program for a Tone Matching Instrument ist die smarte Lösung für Unternehmen, die bei Farbgenauigkeit keine Kompromisse machen. Die Software erkennt Farbabweichungen zwischen Mustern vollautomatisch, beschreibt sie verständlich und sorgt so für gleichbleibend hohe Produktqualität – schnell, visuell und präzise. Perfekt für alle, die Farbe zur Vertrauenssache machen.
-------------------------

Thanks,
Gerold

Target Market(s)

IT Professionals from any sector

Industry/Entity Type

Healthcare and other

Coding

Coded - Design and coding required

Number of Pages Required

1 page

Font styles to use
Sans Serif

Colors
0054AA
0677BA
7BADD7
CADEEF
E8F1F8
0094D4
00A9DD
6FCCEA
C7EBF8
E9F6FB
00AB8E
00BBA5
67D7C9
C6EFE9
E9F9F6

Requirements
Must have
• Please see description
Nice to have
• On the landing page the company should introduced with a small text (max 250 words) followed by a section with a short text to one of our products nearby a graphic visualising the architecture of the product. The menue should be on top and fixed during scrolling and consist of the menue items home, solutions, who are we and a contact button. There should be a footer for linking social media, rights and Impressum. Only as an idea not a must. The very first view on the landing page could also be the menue bar and below of it a transparent unsharp photo (e.g. datacenter, lines of code, both ;) with the company name in the center.
Should not have
• Please see description

```html
<!DOCTYPE html>
<html lang="en">
<head>
<meta charset="utf-8">
<title>QR.KA Horizon – Software Engineering &amp; IT</title>
<link rel="stylesheet" href="https://fonts.googleapis.com/css2?family=Jost:wght@300;400;500;600&family=Plus+Jakarta+Sans:wght@500;600;700&display=swap">
<style>
:root{
  --blue-deep:#0054AA;
  --blue:#0677BA;
  --blue-soft:#7BADD7;
  --blue-pale:#E2EDF8;
  --teal:#00BBA5;
  --teal-dark:#00AB8E;
  --ink:#111111;
  --text:#4a4a4a;
  --band:#1D4F9A;
  --footer:#1B1B1B;
  --white:#ffffff;
}
*{margin:0;padding:0;box-sizing:border-box}
html,body{width:1200px;height:3818px;overflow:hidden}
body{position:relative;font-family:'Jost',sans-serif;color:var(--ink);background:var(--white)}
.abs{position:absolute}
.accent{color:var(--blue);font-weight:500}
.btn{position:absolute;display:flex;align-items:center;justify-content:center;border-radius:22px;background:var(--teal);color:var(--white);font-family:'Plus Jakarta Sans',sans-serif;font-weight:700;font-size:15px}
.body-text{font-size:13.6px;line-height:28.5px;color:var(--text);font-weight:400}

/* header */
.site-header{position:absolute;left:0;top:0;width:1200px;height:72px;background:var(--white);z-index:5}
.brand{position:absolute;left:110px;top:14px;display:flex;align-items:center;gap:14px}
.brand-dot{width:58px;height:58px;border-radius:50%;background:linear-gradient(135deg,var(--teal),var(--blue))}
.brand-name{font-family:'Plus Jakarta Sans',sans-serif;font-weight:600;font-size:28px;color:var(--ink)}
.nav a{position:absolute;top:24px;font-size:19px;color:var(--ink);text-decoration:none}
.nav .active{color:var(--blue)}
.nav-contact{left:973px;top:16px;width:114px;height:41px;font-size:16px}

/* hero */
.hero{position:absolute;left:0;top:72px;width:1200px;height:592px;background:radial-gradient(ellipse at 50% 45%,#2a6fb8 0%,#123d78 30%,#071a38 65%,#02060f 100%)}
.hero-title{position:absolute;left:0;top:218px;width:1200px;text-align:center;font-family:'Plus Jakarta Sans',sans-serif;font-weight:700;font-size:80px;color:var(--white)}
.hero-sub{position:absolute;left:280px;top:324px;width:640px;text-align:center;font-family:'Plus Jakarta Sans',sans-serif;font-weight:600;font-size:21px;line-height:31px;color:var(--white)}
.hero-btn{left:538px;top:404px;width:114px;height:40px;background:var(--white);color:var(--ink);font-size:15px;font-weight:600}

/* who */
.who-photo{position:absolute;left:143px;top:753px;width:414px;height:414px;border-radius:50%;border:10px solid transparent;background:linear-gradient(#cfd6de,#8c99a8) padding-box,linear-gradient(160deg,var(--blue),var(--teal)) border-box}
.who-photo::after{content:"";position:absolute;inset:8px;border-radius:50%;border:6px solid var(--white)}
.section-title{font-size:42px;font-weight:400;color:var(--ink)}

/* products */
.products{position:absolute;left:0;top:1249px;width:1200px;height:517px;background:var(--blue-pale)}
.arch{position:absolute;left:630px;top:56px;width:475px;height:395px;border-radius:24px;background:radial-gradient(circle at 50% 45%,#7BADD7 0%,#C7DDF1 60%,transparent 75%)}

/* solutions */
.card{position:absolute;top:2024px;width:311px;height:368px;border-radius:8px;overflow:hidden}
.card-fill{position:absolute;inset:0}
.card-label{position:absolute;left:24px;color:var(--white);font-family:'Plus Jakarta Sans',sans-serif;font-weight:600;font-size:16.5px;line-height:26px}
.card-open{background:var(--white);box-shadow:0 2px 12px rgba(0,0,0,.12)}
.arrow{position:absolute;top:2206px;width:22px;height:22px;border-radius:50%;display:flex;align-items:center;justify-content:center}

/* cta */
.cta{position:absolute;left:0;top:2477px;width:1200px;height:263px;background:var(--band)}

/* why */
.why-item h3{font-size:22px;font-weight:400;color:var(--ink);margin-bottom:8px}
.why-item p{font-size:15px;line-height:30px;color:var(--text)}
.icon-disc{position:absolute;width:88px;height:88px;border-radius:50%;display:flex;align-items:center;justify-content:center}

/* footer */
.footer{position:absolute;left:0;top:3368px;width:1200px;height:450px;background:var(--footer);color:var(--white)}
.f-col h4{font-family:'Plus Jakarta Sans',sans-serif;font-weight:600;font-size:21px;margin-bottom:18px}
.f-col a{display:block;color:var(--white);text-decoration:none;font-family:'Plus Jakarta Sans',sans-serif;font-weight:500;font-size:15px;line-height:34px}
.contact-row{display:flex;align-items:center;gap:14px;font-family:'Plus Jakarta Sans',sans-serif;font-weight:500;font-size:15px;height:40px}
.c-icon{width:24px;height:24px;border-radius:50%;background:var(--white);display:flex;align-items:center;justify-content:center}
.social{display:flex;align-items:center;gap:16px;font-family:'Plus Jakarta Sans',sans-serif;font-weight:500;font-size:15px;height:40px}
.social span.dot{width:18px;height:18px;border-radius:50%;border:2px solid var(--white)}
</style>
</head>
<body>

<header class="site-header">
  <div class="brand"><div class="brand-dot"></div><div class="brand-name">QR.KA Horizon</div></div>
  <nav class="nav">
    <a class="active" style="left:595px">Home</a>
    <a style="left:698px">Solution</a>
    <a style="left:820px">Who We Are</a>
  </nav>
  <div class="btn nav-contact">Contact</div>
</header>

<section class="hero" role="img" aria-label="Data center corridor lit by glowing blue binary code">
  <h1 class="hero-title">QR.KA Horizon</h1>
  <p class="hero-sub">Innovating at the intersection of software engineering and IT to drive transformative results.</p>
  <div class="btn hero-btn">Get Started</div>
</section>

<section class="who">
  <div class="who-photo" role="img" aria-label="Team meeting around a laptop in a bright office"></div>
  <h2 class="abs section-title" style="left:644px;top:738px">Who <span class="accent">We Are</span></h2>
  <div class="abs body-text" style="left:644px;top:808px;width:440px">
    <p>At QR.KA Horizon, we believe that software engineering and IT are not just disciplines—they are the backbone of innovation. Founded on the principle that technology should empower, not just function, we specialize in crafting software solutions that are both powerful and seamlessly integrated into existing IT landscapes.</p>
    <p style="margin-top:4px">Our mission is simple: to bridge the gap between visionary software development and real-world IT applications. We don't just build software; we create intelligent systems that adapt, evolve, and drive businesses forward.</p>
  </div>
  <div class="btn" style="left:644px;top:1118px;width:114px;height:40px">Read More</div>
</section>

<section class="products">
  <h2 class="abs section-title" style="left:108px;top:48px">Our <span class="accent">Products</span></h2>
  <p class="abs" style="left:111px;top:116px;font-size:16px;color:var(--ink)">Empowering Businesses with Intelligent Workflow Automation</p>
  <div class="abs body-text" style="left:108px;top:153px;width:430px;line-height:29px">
    <p>At QR.KA Horizon, we develop cutting-edge products designed to revolutionize the way businesses operate. Our solutions are engineered for performance, scalability, and seamless integration into any IT landscape.</p>
    <p style="margin-top:14px">TideFlow is our flagship product, designed to automate complex business processes with ease. It integrates advanced AI algorithms to optimize workflows, reduce manual efforts, and improve operational efficiency.</p>
  </div>
  <div class="btn" style="left:115px;top:415px;width:113px;height:40px">Read More</div>
  <div class="arch" role="img" aria-label="Isometric illustration of servers, cloud nodes and laptops linked in a network"></div>
</section>

<section class="solutions">
  <h2 class="abs section-title" style="left:0;top:1846px;width:1200px;text-align:center">Our <span class="accent">Solutions</span></h2>
  <p class="abs body-text" style="left:240px;top:1916px;width:720px;text-align:center;font-size:13.4px;line-height:26.5px">At QR.KA Horizon, we deliver advanced technology solutions designed to transform businesses through seamless integration and innovative software development. Our offerings are tailored to meet the dynamic demands of modern IT landscapes, ensuring scalability, efficiency, and future-proofing.</p>

  <div class="arrow" style="left:35px;background:var(--teal-dark)"><svg width="10" height="10" viewBox="0 0 10 10"><path d="M3 1l4 4-4 4" stroke="#fff" stroke-width="2" fill="none"/></svg></div>
  <div class="arrow" style="left:1124px;background:#9a9a9a"><svg width="10" height="10" viewBox="0 0 10 10"><path d="M3 1l4 4-4 4" stroke="#fff" stroke-width="2" fill="none"/></svg></div>

  <div class="card" style="left:110px">
    <div class="card-fill" role="img" aria-label="Engineer designing a car model on a monitor" style="background:linear-gradient(180deg,#7e9cbc 0%,#3d5c80 60%,#1c2c44 100%)"></div>
    <div class="card-label" style="top:306px">Software Development &amp;<br>Customization</div>
  </div>

  <div class="card card-open" style="left:442px">
    <div class="abs" role="img" aria-label="Technician with a tablet between server racks" style="left:0;top:0;width:311px;height:196px;background:linear-gradient(180deg,#3d6a9a,#12294a)"></div>
    <div class="abs" style="left:240px;top:165px;width:52px;height:52px;border-radius:50%;background:var(--white);display:flex;align-items:center;justify-content:center">
      <svg width="30" height="30" viewBox="0 0 30 30" fill="none" stroke="var(--blue)" stroke-width="1.8"><rect x="6" y="6" width="18" height="7" rx="2"/><rect x="6" y="15" width="18" height="7" rx="2"/><path d="M15 22v4M9 26h12"/></svg>
    </div>
    <p class="abs" style="left:18px;top:218px;font-size:17px;color:var(--blue);font-weight:500">IT Infrastructure Integration</p>
    <p class="abs body-text" style="left:18px;top:248px;width:280px;font-size:13px;line-height:26.5px">Our IT integration solutions bridge the gap between legacy systems and modern technologies.</p>
  </div>

  <div class="card" style="left:774px">
    <div class="card-fill" role="img" aria-label="Hand on a laptop with floating analytics dashboards" style="background:linear-gradient(160deg,#9fb8d2 0%,#4f6f93 55%,#1e3250 100%)"></div>
    <div class="card-label" style="top:316px">Data Management &amp; Analytics</div>
  </div>
</section>

<section class="cta">
  <h2 class="abs" style="left:108px;top:62px;font-family:'Plus Jakarta Sans',sans-serif;font-weight:600;font-size:43px;line-height:57px;color:var(--white)">Let's Build the Future<br>Together—Get in Touch!</h2>
  <p class="abs" style="left:672px;top:72px;width:440px;font-family:'Plus Jakarta Sans',sans-serif;font-weight:500;font-size:14.5px;line-height:29px;color:var(--white)">From startups to global enterprises, our solutions have helped businesses across industries innovate, integrate, and excel.</p>
  <div class="btn" style="left:672px;top:140px;width:112px;height:40px;font-size:15px">Conatct Us</div>
</section>

<section class="why">
  <h2 class="abs section-title" style="left:0;top:2812px;width:1200px;text-align:center">Why Choose <span class="accent">QR.KA Horizon?</span></h2>

  <div class="abs" style="left:456px;top:3068px;width:288px;text-align:center;font-family:'Plus Jakarta Sans',sans-serif;font-weight:700;font-size:34px;color:var(--blue)">QR.KA Horizon</div>

  <div class="abs why-item" style="left:110px;top:2936px;width:230px"><h3>&nbsp;Innovative Thinking</h3><p>We push the boundaries of technology to deliver visionary solutions.</p></div>
  <div class="icon-disc" style="left:360px;top:2940px;background:var(--blue)">
    <svg width="40" height="40" viewBox="0 0 40 40" fill="none" stroke="#fff" stroke-width="2"><circle cx="20" cy="18" r="8"/><path d="M16 30h8M17 34h6M20 4v4M8 8l3 3M32 8l-3 3M4 18h4M32 18h4"/></svg>
  </div>

  <div class="abs why-item" style="left:848px;top:2936px;width:250px"><h3>&nbsp;Agile Approach</h3><p>Flexibility and adaptability are at the core of everything we do.</p></div>
  <div class="icon-disc" style="left:735px;top:2934px;background:var(--teal-dark)">
    <svg width="42" height="42" viewBox="0 0 42 42" fill="none" stroke="#fff" stroke-width="2.2"><path d="M33 16a13 13 0 0 0-24-3M9 26a13 13 0 0 0 24 3"/><path d="M9 7v6h6M33 35v-6h-6"/><circle cx="21" cy="21" r="5"/></svg>
  </div>

  <div class="abs why-item" style="left:110px;top:3153px;width:230px"><h3>&nbsp;Seamless Integration</h3><p>Our solutions are designed to work effortlessly with your existing IT infrastructure.</p></div>
  <div class="icon-disc" style="left:360px;top:3158px;background:var(--teal)">
    <svg width="44" height="44" viewBox="0 0 44 44" fill="none" stroke="#fff" stroke-width="2.2"><path d="M13 28a8 8 0 0 1 1-16 10 10 0 0 1 18 3 7 7 0 0 1-1 13"/><circle cx="22" cy="24" r="5"/><path d="M22 29v8M15 33l4-4M29 33l-4-4"/></svg>
  </div>

  <div class="abs why-item" style="left:852px;top:3160px;width:230px"><h3>&nbsp;Expert Team</h3><p>Our specialists bring deep expertise in both software engineering and IT systems.</p></div>
  <div class="icon-disc" style="left:730px;top:3164px;background:var(--blue)">
    <svg width="44" height="44" viewBox="0 0 44 44" fill="#fff"><circle cx="22" cy="12" r="5"/><circle cx="11" cy="19" r="4"/><circle cx="33" cy="19" r="4"/><path d="M14 34a8 8 0 0 1 16 0z"/><path d="M4 32a7 7 0 0 1 12-4l-3 4z"/><path d="M40 32a7 7 0 0 0-12-4l3 4z"/></svg>
  </div>
</section>

<footer class="footer">
  <div class="abs" style="left:112px;top:48px;display:flex;align-items:center;gap:18px">
    <div style="width:110px;height:110px;border-radius:50%;background:linear-gradient(135deg,var(--teal),var(--blue))"></div>
    <div style="font-family:'Plus Jakarta Sans',sans-serif;font-weight:600;font-size:40px;color:var(--white)">QR.KA Horizon</div>
  </div>
  <div class="abs" style="left:558px;top:87px;width:530px;height:58px;border-radius:30px;background:var(--white)">
    <span class="abs" style="left:50px;top:19px;font-family:'Plus Jakarta Sans',sans-serif;font-size:14px;color:#333">Enter Email Address</span>
    <div class="abs" style="left:368px;top:0;width:162px;height:58px;border-radius:30px;background:#2A6DB5;color:#fff;display:flex;align-items:center;justify-content:center;font-family:'Plus Jakarta Sans',sans-serif;font-weight:700;font-size:15px">Subscribe</div>
  </div>

  <div class="abs f-col" style="left:110px;top:212px"><h4>Quick Links</h4><a>Home</a><a>Solution</a><a>Who We Are</a><a>Contact</a></div>
  <div class="abs f-col" style="left:351px;top:212px"><h4>Help Links</h4><a>Privacy policy</a><a>Terms &amp; Conditions</a><a>Disclaimer</a></div>
  <div class="abs f-col" style="left:599px;top:212px"><h4>Contact Info</h4>
    <div class="contact-row"><span class="c-icon"><svg width="12" height="14" viewBox="0 0 12 14"><path d="M6 0a5 5 0 0 0-5 5c0 4 5 9 5 9s5-5 5-9a5 5 0 0 0-5-5z" fill="#1B1B1B"/><circle cx="6" cy="5" r="1.8" fill="#fff"/></svg></span>12 Harbor Lane, Northvale 437916</div>
    <div class="contact-row"><span class="c-icon"><svg width="12" height="12" viewBox="0 0 12 12"><path d="M2 1l2 0 1 3-1.5 1a7 7 0 0 0 3.5 3.5L8 7l3 1v2a1 1 0 0 1-1 1A9 9 0 0 1 1 2a1 1 0 0 1 1-1z" fill="#1B1B1B"/></svg></span>+1 555 014 2290</div>
    <div class="contact-row"><span class="c-icon"><svg width="13" height="10" viewBox="0 0 13 10"><rect x="0.5" y="0.5" width="12" height="9" rx="1" fill="#1B1B1B"/><path d="M1 1l5.5 4.5L12 1" stroke="#fff" fill="none"/></svg></span>hello@qrkahorizon.net</div>
  </div>
  <div class="abs f-col" style="left:960px;top:204px"><h4 style="margin-left:21px">Follow Us</h4>
    <div class="social" style="margin-left:18px"><span class="dot"></span>Friendwall</div>
    <div class="social" style="margin-left:18px"><span class="dot"></span>Snapgrid</div>
    <div class="social" style="margin-left:18px"><span class="dot"></span>Chirpline</div>
    <div class="social" style="margin-left:18px"><span class="dot"></span>Workmesh</div>
  </div>

  <div class="abs" style="left:110px;top:414px;width:980px;height:1px;background:#5a5a5a"></div>
  <p class="abs" style="left:0;top:424px;width:1200px;text-align:center;font-family:'Plus Jakarta Sans',sans-serif;font-size:11px;color:#ddd">Copyright © 2025 QR.KA Horizon. All rights reserved.</p>
</footer>

</body>
</html>
```